Profesional personal website needs design and business card

I need a business card with my professional name as a logo "Dorian Vitality" for my business. I am a Wellness Coach, consultant and trainer. So it should be professional, wellness oriented and modern.

Target Market(s)

Private clients, governments, corporations. Luxury and high market.

Industry/Entity Type

Health And Wellness

Contact Information for Business Card

Dorian Vitality should be the logo

Colors

Designer to choose colors to be used in the design.

Requirements
Must have
• Dorian Vitality
• Name: Tomás Lirandel
• Wellness Coach, Consultant & Trainer.
• Website: www.dorianvitality-example.com
• Phone:
• Spain (+34) 612 480 317
• (USA) +1 (555) 610 4829
Nice to have
• The most important is the design of "Dorian Vitality", as this is going to be my personal brand logo. It should be professional, wellness, high end and actual.
Should not have
• no golds, no baroque style..

```html
<!DOCTYPE html>
<html lang="en">
<head>
<meta charset="utf-8">
<title>Dorian Vitality – Business Card</title>
<link rel="stylesheet" href="https://fonts.googleapis.com/css2?family=Montserrat:wght@600&family=Roboto:wght@300;400;500&display=swap">
<style>
  :root {
    --page: #ffffff;
    --lime-soft: #e6eb9e;
    --lime: #d4df2b;
    --clay: #b8927a;
    --clay-light: #c8a386;
    --peach: #fdd18e;
    --navy: #0f2d35;
    --brown: #8a5a2b;
    --rule: #a97c55;
    --ink: #1a1a1a;
  }
  html, body {
    margin: 0;
    padding: 0;
    width: 1000px;
    height: 1200px;
    overflow: hidden;
    background: var(--page);
  }
  .sheet {
    position: relative;
    width: 1000px;
    height: 1200px;
  }
  .card {
    position: absolute;
    left: 106px;
    width: 792px;
    height: 453px;
    display: block;
  }
  .card--front { top: 95px; }
  .card--back { top: 623px; }
  .tone-start { stop-color: var(--lime-soft); }
  .tone-mid { stop-color: #ffffff; }
  .tone-clay { stop-color: var(--clay-light); stop-opacity: 0.45; }
  .tone-end { stop-color: var(--peach); }
  .brand-dot { fill: var(--lime); }
  .brand-name {
    font-family: "Montserrat", sans-serif;
    font-weight: 600;
    fill: var(--navy);
  }
  .person-name {
    font-family: "Roboto", sans-serif;
    font-weight: 500;
    font-size: 66px;
    fill: var(--brown);
  }
  .person-role {
    font-family: "Roboto", sans-serif;
    font-weight: 300;
    font-size: 23px;
    fill: var(--ink);
  }
  .rule { stroke: var(--rule); stroke-width: 5; }
  .contact {
    font-family: "Roboto", sans-serif;
    font-weight: 400;
    font-size: 32px;
    fill: var(--ink);
  }
  .icon-disc { fill: var(--lime); }
  .icon-glyph { fill: #111; }
  .icon-line { stroke: var(--lime); stroke-width: 3; fill: none; }
</style>
</head>
<body>
<main class="sheet">

  <svg class="card card--front" viewBox="0 0 1394 797" role="group" aria-label="Business card front">
    <defs>
      <linearGradient id="card-wash" x1="0" y1="0" x2="1" y2="1">
        <stop offset="0" class="tone-start"/>
        <stop offset="0.32" class="tone-mid"/>
        <stop offset="0.62" class="tone-mid"/>
        <stop offset="0.82" class="tone-clay"/>
        <stop offset="1" class="tone-end"/>
      </linearGradient>
    </defs>
    <g role="img" aria-label="Sweeping background curves in lime, clay and peach">
      <rect class="card-wash" width="1394" height="797" fill="url(#card-wash)"/>
    </g>

    <g class="brand">
      <circle class="brand-dot" cx="697" cy="290" r="92"/>
      <text class="brand-name" x="709" y="525" text-anchor="middle" font-size="92" letter-spacing="24">Dorian</text>
      <text class="brand-name" x="697" y="612" text-anchor="middle" font-size="66">Vitality</text>
    </g>
  </svg>

  <svg class="card card--back" viewBox="0 0 1394 797" role="group" aria-label="Business card back">
    <g role="img" aria-label="Sweeping background curves in lime, clay and peach">
      <rect class="card-wash" width="1394" height="797" fill="url(#card-wash)"/>
    </g>

    <text class="person-name" x="695" y="210" text-anchor="middle">Tomás Lirandel</text>
    <text class="person-role" x="695" y="250" text-anchor="middle">Wellness Coach, Consultant &amp; Trainer</text>
    <line class="rule" x1="486" y1="274" x2="877" y2="273"/>
    <line class="rule" x1="512" y1="297" x2="903" y2="296"/>
    <line class="rule" x1="486" y1="320" x2="877" y2="319"/>

    <g class="contact-phone">
      <circle class="icon-disc" cx="492" cy="451" r="36"/>
      <path class="icon-glyph" d="M474 431 l8 -4 l9 14 l-6 5 c3 7 8 12 15 16 l6 -5 l13 10 l-4 8 c-3 4 -9 5 -14 2 c-13 -7 -24 -19 -30 -32 c-2 -5 -1 -10 3 -14 Z"/>
      <text class="contact" x="542" y="440">Spain : (+34) 612 480 317</text>
      <text class="contact" x="542" y="480">USA&#160;&#160;&#160;&#160;: +1 (555) 610 4829</text>
    </g>

    <g class="contact-web">
      <circle class="icon-disc" cx="492" cy="566" r="36"/>
      <circle class="icon-glyph" cx="492" cy="566" r="24"/>
      <ellipse class="icon-line" cx="492" cy="566" rx="10" ry="24"/>
      <line class="icon-line" x1="468" y1="566" x2="516" y2="566"/>
      <text class="contact" x="545" y="577">www.dorianvitality-example.com</text>
    </g>
  </svg>

</main>
</body>
</html>
```